Veterinary Pylon

My veterinary clinic is not clearly visible from the street and I want to place a Pylon next to my driveway. I want a modern, elegant straight Design, the Photo shows the sheduled place. One can see the clinic on our Homepage: www.tailbright-vethaus.at
The last pictures are examples for pylones I like

Target Market(s)

the passing cars often miss my entry...I want to show where to turn left

Colors
3276b5
33a6d7
00a990

Requirements
Must have
• High value, simple elegance, size: 250cm (high) x 100cm (width)
Nice to have
• Our Logo, arrow(?)

A special Text is not necessary but this will be an option:

Biegen sie hier ab und wir biegen es wieder hin!
Should not have
• Too much Color, the colors I have chosen are the possible colors but it‘s not necessary to use them.

```html
<!DOCTYPE html>
<html lang="de">
<head>
<meta charset="utf-8">
<title>Tailbright Vethaus – Pylon</title>
<link href="https://fonts.googleapis.com/css2?family=Montserrat:wght@400;500;600;700&display=swap" rel="stylesheet">
<style>
  :root {
    --navy: #2a4a8c;
    --sky: #3bb6de;
    --white: #ffffff;
    --backdrop: #eef1f4;
    --steel-dark: #8a8d90;
    --steel-light: #d6d8da;
  }
  * { margin: 0; padding: 0; box-sizing: border-box; }
  html, body { width: 818px; height: 1200px; overflow: hidden; }
  body {
    background: var(--backdrop);
    font-family: "Montserrat", Arial, sans-serif;
    position: relative;
  }
  .post {
    position: absolute;
    width: 37px;
    background: linear-gradient(90deg, var(--steel-dark), var(--steel-light) 45%, var(--steel-dark));
  }
  .post--left { left: 236px; }
  .post--right { left: 429px; }
  .post--upper { top: 304px; height: 28px; }
  .post--lower { top: 551px; height: 27px; }

  .panel-top {
    position: absolute;
    left: 145px; top: 85px;
    width: 411px; height: 219px;
    background: var(--navy);
  }
  .name-board {
    position: absolute;
    left: 106px; top: 332px;
    width: 606px; height: 219px;
    background: var(--white);
    padding: 13px;
  }
  .name-board__frame {
    width: 100%; height: 100%;
    border: 2px solid var(--navy);
    display: flex;
    align-items: center;
    justify-content: center;
    gap: 22px;
  }
  .name-board__dot {
    width: 54px; height: 54px;
    border-radius: 50%;
    background: var(--sky);
    flex: none;
  }
  .name-board__name {
    color: var(--navy);
    font-weight: 700;
    font-size: 44px;
    line-height: 1.05;
    letter-spacing: 0.5px;
  }

  .panel-info {
    position: absolute;
    left: 145px; top: 578px;
    width: 411px; height: 537px;
    background: var(--navy);
    color: var(--white);
  }
  .headline {
    position: absolute;
    left: 48px; top: 38px;
    font-weight: 600;
    font-size: 38px;
    line-height: 45px;
  }
  .hours {
    position: absolute;
    left: 50px; top: 208px;
    list-style: none;
  }
  .hours__group {
    border-left: 1.5px solid var(--white);
    padding-left: 9px;
    height: 62px;
    margin-bottom: 18px;
  }
  .hours__day {
    color: var(--sky);
    font-weight: 600;
    font-size: 15.5px;
    line-height: 21px;
  }
  .hours__time {
    font-weight: 400;
    font-size: 16px;
    line-height: 20.5px;
  }
  .web {
    position: absolute;
    left: 50px; top: 459px;
    font-weight: 600;
    font-size: 20px;
  }
</style>
</head>
<body>
  <div class="post post--left post--upper"></div>
  <div class="post post--right post--upper"></div>
  <div class="post post--left post--lower"></div>
  <div class="post post--right post--lower"></div>

  <div class="panel-top"></div>

  <div class="name-board">
    <div class="name-board__frame">
      <span class="name-board__dot"></span>
      <span class="name-board__name">Tailbright<br>Vethaus</span>
    </div>
  </div>

  <div class="panel-info">
    <h1 class="headline">Biegen Sie ein,<br>dann biegen wir<br>es hin!</h1>
    <ul class="hours">
      <li class="hours__group">
        <p class="hours__day">MONDAY - FRIDAY</p>
        <p class="hours__time">08:00 - 12:00</p>
        <p class="hours__time">14:00 - 19:00</p>
      </li>
      <li class="hours__group">
        <p class="hours__day">SATURDAY</p>
        <p class="hours__time">08:00 - 12:00</p>
        <p class="hours__time">17:00 - 18:00</p>
      </li>
      <li class="hours__group">
        <p class="hours__day">SUNDAY</p>
        <p class="hours__time">10:00 am - 11:00 am</p>
        <p class="hours__time">17:00 - 18:00</p>
      </li>
    </ul>
    <p class="web">www.tailbright-vethaus.at</p>
  </div>
</body>
</html>
```